Business Card Design for Training Business

Clear Path Coaching is a new business that delivers training and other services with a focus on topics related to mental health and wellbeing, for example, Wellmind Response Course, Resilience etc. We have a strong focus on evidence-based psychology and neuroscience. I have a logo which I will upload with the brief, so please consider colours that work well with the logo.
Target Market(s)
Adults, workplaces (particularly government and not-for-profits)
Industry/Entity Type
Business
Contact Information for Business Card
Head Strong TrainingSamantha SellwoodDirector0438 770 850sam@headstrongtraining.com.auwww.headstrongtraining.com.au

```html
<!DOCTYPE html>
<html lang="en">
<head>
<meta charset="utf-8">
<title>Clear Path Coaching – Business Card</title>
<link rel="stylesheet" href="https://fonts.googleapis.com/css2?family=Arimo:wght@400&display=swap">
<style>
  :root {
    --page-bg: #d8d3cb;
    --card-black: #0b0b0c;
    --card-sheen: #1d1e20;
    --teal: #2fb3b6;
    --teal-deep: #1f9a9d;
    --rule-dark: #2a2a2a;
    --ink-white: #ffffff;
    --ink-muted: #4a4a4a;
  }
  * { margin: 0; padding: 0; box-sizing: border-box; }
  html, body {
    width: 1200px; height: 892px; overflow: hidden;
    background: var(--page-bg);
    font-family: "Arimo", Arial, sans-serif;
  }
  .business-card {
    position: absolute; left: 100px; top: 140px;
    width: 1000px; height: 611px;
    background: linear-gradient(125deg, var(--card-black) 0%, var(--card-sheen) 45%, var(--card-black) 70%, #151617 100%);
    border-radius: 4px;
    overflow: hidden;
    box-shadow: 0 10px 30px rgba(0,0,0,.25);
  }
  .brand {
    position: absolute; left: 50px; top: 95px; width: 450px;
    display: flex; flex-direction: column; align-items: center;
  }
  .brand-circle {
    width: 190px; height: 190px; border-radius: 50%;
    border: 3px solid var(--teal);
  }
  .brand-name {
    margin-top: 36px;
    font-size: 34px; font-weight: 400; letter-spacing: 4px;
    color: var(--ink-muted); white-space: nowrap;
  }
  .divider {
    position: absolute; left: 528px; top: 80px;
    width: 2px; height: 395px; background: var(--teal);
  }
  .person { position: absolute; left: 560px; top: 145px; color: var(--ink-white); }
  .person-name { font-size: 44px; line-height: 1; white-space: nowrap; }
  .person-role { font-size: 29px; line-height: 1.1; margin-top: 2px; }
  .contact-list {
    position: absolute; left: 560px; top: 300px; right: 50px;
    list-style: none; color: var(--ink-white);
    font-size: 21px;
  }
  .contact-list li { display: flex; align-items: center; height: 34px; white-space: nowrap; }
  .contact-icon { width: 20px; height: 20px; margin-right: 14px; flex: none; }
  .band-rule {
    position: absolute; left: 0; bottom: 86px; width: 100%; height: 6px;
    background: var(--rule-dark);
  }
  .teal-band {
    position: absolute; left: 0; bottom: 0; width: 100%; height: 86px;
    background: linear-gradient(90deg, var(--teal-deep), var(--teal) 60%, #45bfc2);
  }
</style>
</head>
<body>
  <article class="business-card">
    <div class="brand">
      <div class="brand-circle"></div>
      <div class="brand-name">Clear Path Coaching</div>
    </div>

    <div class="divider"></div>

    <div class="person">
      <div class="person-name">Rebecca Tanfield</div>
      <div class="person-role">Director</div>
    </div>

    <ul class="contact-list">
      <li>
        <svg class="contact-icon" viewBox="0 0 22 22" aria-hidden="true">
          <rect width="22" height="22" rx="2" fill="#fff"/>
          <path d="M6 5c1-1 2 0 3 2s0 2-.5 2.5c1 2 2 3 4 4 .5-.5 1-1.5 2.5-.5s3 2 2 3-3 1.5-6-1.5S5 6 6 5z" fill="#0b0b0c"/>
        </svg>
        0491 362 517
      </li>
      <li>
        <svg class="contact-icon" viewBox="0 0 22 22" aria-hidden="true">
          <rect width="22" height="22" rx="2" fill="#fff"/>
          <rect x="4" y="6" width="14" height="10" fill="#0b0b0c"/>
          <path d="M4.5 6.5 11 12l6.5-5.5" stroke="#fff" stroke-width="1.3" fill="none"/>
        </svg>
        bec@clearpathcoaching.example.au
      </li>
      <li>
        <svg class="contact-icon" viewBox="0 0 22 22" aria-hidden="true">
          <rect width="22" height="22" rx="2" fill="#fff"/>
          <circle cx="11" cy="11" r="7" fill="none" stroke="#0b0b0c" stroke-width="1.6"/>
          <ellipse cx="11" cy="11" rx="3" ry="7" fill="none" stroke="#0b0b0c" stroke-width="1.3"/>
          <path d="M4 11h14" stroke="#0b0b0c" stroke-width="1.3"/>
        </svg>
        www.clearpathcoaching.example.au
      </li>
    </ul>

    <div class="band-rule"></div>
    <div class="teal-band"></div>
  </article>
</body>
</html>
```